Irrigation Business needs their business cards modernised and revamped

I would like to keep my current logo, colours and revamp the format of the card.

I would like the card to be clean yet important.

Im not sure if you include texture but i would like the named logo to be indented into the card etc.

show me something alive and free something thats clinical to the point yet has a feel of achievement. i would like people to go nice card.

Target Market(s)

high end clients, corporate, sports field manger, the guys that make the decisions

Industry/Entity Type

Business

Contact Information for Business Card

nformation to be included

Dean Harlow (Director)
0487305526
dean@kolvat.biz
www.kestonfieldworks.com

instagram logo
google logo
facebook logo

Colors

Designer to choose colors to be used in the design.

Requirements
Nice to have
• indentations a really nice feel to the card good texture

```html
<!DOCTYPE html>
<html lang="en">
<head>
<meta charset="utf-8">
<title>Keston Fieldworks – Business Card</title>
<link href="https://fonts.googleapis.com/css2?family=Open+Sans:wght@400;600;700;800&display=swap" rel="stylesheet">
<style>
  :root {
    --bg: #1d1d1d;
    --card-white: #f7f8f8;
    --brand-blue: #2d5fa8;
    --wave-blue: #2b9fd6;
    --brand-green: #1f9a4a;
    --text-grey: #555b60;
    --back-green-light: #74b25e;
    --back-green-dark: #1f9954;
    --back-mark: #2a8f4c;
  }
  * { margin: 0; padding: 0; box-sizing: border-box; }
  html, body { width: 960px; height: 1200px; overflow: hidden; background: var(--bg); }
  body { font-family: "Open Sans", Arial, sans-serif; position: relative; }

  .card {
    position: absolute; left: 130px; width: 700px; height: 400px;
    border-radius: 34px; overflow: hidden;
    box-shadow: 0 14px 30px rgba(0,0,0,.45);
  }
  .card--front { top: 110px; background: var(--card-white); }
  .card--back {
    top: 680px;
    background: radial-gradient(ellipse at 55% 45%, var(--back-green-light) 0%, var(--back-green-dark) 70%);
  }

  .card__waves { position: absolute; inset: 0; }

  .holder { position: absolute; left: 52px; top: 58px; }
  .holder__name { font-size: 31px; font-weight: 800; color: var(--brand-green); letter-spacing: .5px; line-height: 1.1; }
  .holder__role { font-size: 25px; font-weight: 400; color: var(--text-grey); line-height: 1.2; }

  .brand { position: absolute; right: 40px; top: 42px; width: 300px; text-align: center; }
  .brand__mark {
    width: 96px; height: 96px; margin: 0 auto 14px; border-radius: 50%;
    border: 5px solid var(--brand-blue);
  }
  .brand__name { font-size: 27px; font-weight: 800; color: var(--brand-blue); letter-spacing: .3px; }

  .contacts { position: absolute; left: 44px; top: 232px; list-style: none; }
  .contacts__item {
    display: flex; align-items: center; gap: 14px;
    color: #fff; font-size: 19px; height: 36px;
  }
  .contacts__item svg { width: 20px; height: 20px; flex: none; }

  .social { position: absolute; right: 50px; bottom: 34px; display: flex; gap: 18px; }
  .social__dot { width: 44px; height: 44px; border-radius: 50%; background: #fff; }

  .back-brand { position: absolute; inset: 0; display: flex; flex-direction: column; align-items: center; justify-content: center; gap: 18px; }
  .back-brand__mark { width: 170px; height: 170px; border-radius: 50%; border: 8px solid var(--back-mark); }
  .back-brand__name { font-size: 30px; font-weight: 800; color: var(--back-mark); letter-spacing: 1px; }
</style>
</head>
<body>

<section class="card card--front" aria-label="Business card front">
  <svg class="card__waves" viewBox="0 0 700 400" preserveAspectRatio="none" aria-hidden="true">
    <path d="M0,142 C190,118 320,262 470,270 S640,238 700,218 L700,400 L0,400 Z" fill="var(--wave-blue)"/>
    <path d="M0,168 C190,146 320,290 470,296 S640,266 700,248 L700,400 L0,400 Z" fill="#ffffff"/>
    <path d="M0,173 C190,151 320,295 470,301 S640,271 700,253 L700,400 L0,400 Z" fill="var(--brand-blue)"/>
  </svg>

  <div class="holder">
    <div class="holder__name">DEAN HARLOW</div>
    <div class="holder__role">Director</div>
  </div>

  <div class="brand">
    <div class="brand__mark"></div>
    <div class="brand__name">KESTON FIELDWORKS</div>
  </div>

  <ul class="contacts">
    <li class="contacts__item">
      <svg viewBox="0 0 20 20" fill="none" stroke="#fff" stroke-width="1.8"><rect x="5" y="1.5" width="10" height="17" rx="2"/><line x1="9" y1="15.5" x2="11" y2="15.5"/></svg>
      <span>0487 305 526</span>
    </li>
    <li class="contacts__item">
      <svg viewBox="0 0 20 20" fill="#fff"><path d="M1 4h18v12H1z"/><path d="M1 4l9 7 9-7" fill="none" stroke="#2d5fa8" stroke-width="1.5"/></svg>
      <span>dean@kolvat.biz</span>
    </li>
    <li class="contacts__item">
      <svg viewBox="0 0 20 20" fill="none" stroke="#fff" stroke-width="1.5"><circle cx="10" cy="10" r="8.5"/><ellipse cx="10" cy="10" rx="3.8" ry="8.5"/><line x1="1.5" y1="10" x2="18.5" y2="10"/><line x1="3" y1="5.5" x2="17" y2="5.5"/><line x1="3" y1="14.5" x2="17" y2="14.5"/></svg>
      <span>www.kestonfieldworks.com</span>
    </li>
  </ul>

  <div class="social" aria-label="Social media links">
    <span class="social__dot"></span>
    <span class="social__dot"></span>
    <span class="social__dot"></span>
  </div>
</section>

<section class="card card--back" aria-label="Business card back">
  <div class="back-brand">
    <div class="back-brand__mark"></div>
    <div class="back-brand__name">KESTON FIELDWORKS</div>
  </div>
</section>

</body>
</html>
```